Kelvor Engineers: Why you should hire us keepsake

New design. Open to plastic cards. We are an engineering firm that designs cell phone towers and commercial buildings. Please check out our website www.kelvorstruct.com for more details. We want people to remember our card and for it to be useful if possible. We want the same look and feel on these cards to be translated to other marketing material we may need such as brochures.

Target Market(s)

Architects, Developers and Telecommunication Carriers

Industry/Entity Type

Engineering

Contact Information for Business Card

Card with our company colors, logo, and innovative design with elements related to our industry.

Font styles to use
Sans Serif

Colors
9bcb3c
abd036
0255a3

Requirements
Must have
• Sleek and hip design
Nice to have
• Bright lime green and navy coloring that pops with an innovative design.
Should not have
• A basic and boring design

```html
<!DOCTYPE html>
<html lang="en">
<head>
<meta charset="utf-8">
<title>Kelvor Engineers Business Card</title>
<link href="https://fonts.googleapis.com/css2?family=Oswald:wght@300;400;600&family=Open+Sans:wght@700&display=swap" rel="stylesheet">
<style>
  :root {
    --navy: #0a2d5e;
    --navy-ink: #0b2a5a;
    --lime: #39e600;
    --white: #ffffff;
    --line: #1a1a1a;
    --text: #333333;
    --stage: #e9e7e3;
  }
  * { box-sizing: border-box; margin: 0; padding: 0; }
  html, body { width: 1200px; height: 1200px; overflow: hidden; background: var(--stage); }
  .canvas {
    width: 1200px; height: 1200px;
    display: flex; flex-direction: column; align-items: center; justify-content: center; gap: 60px;
  }
  .card {
    width: 840px; height: 480px;
    box-shadow: 0 6px 18px rgba(0,0,0,.18);
    position: relative;
  }
  /* Front */
  .card-front { background: var(--navy); }
  .brand-frame {
    position: absolute; left: 180px; top: 150px; width: 480px; height: 150px;
    border: 2px solid var(--white);
    padding: 0 28px;
    display: flex; align-items: center; justify-content: center;
  }
  .brand-name {
    font-family: 'Oswald', sans-serif; font-weight: 600; font-size: 48px; line-height: 1;
    color: var(--lime); text-transform: uppercase; letter-spacing: 1px;
    white-space: nowrap; text-align: center;
  }
  .brand-cities {
    position: absolute; left: 180px; top: 318px; width: 480px; text-align: center;
    font-family: 'Oswald', sans-serif; font-weight: 300; font-size: 19px;
    color: var(--white); letter-spacing: 1px; text-transform: uppercase; white-space: nowrap;
  }
  /* Back */
  .card-back { background: var(--white); }
  .contact-table {
    position: absolute; left: 90px; top: 70px; width: 660px; height: 340px;
    border: 2px solid var(--line);
    display: grid; grid-template-rows: 1.15fr 1fr 0.8fr 0.9fr;
  }
  .row { border-bottom: 2px solid var(--line); display: flex; align-items: center; justify-content: center; }
  .row:last-child { border-bottom: none; }
  .row-split { display: grid; grid-template-columns: 1fr 1fr; align-items: stretch; }
  .row-split .cell { display: flex; align-items: center; justify-content: center; }
  .row-split .cell + .cell { border-left: 2px solid var(--line); }
  .person-name {
    font-family: 'Oswald', sans-serif; font-weight: 600; font-size: 40px;
    color: var(--navy-ink); letter-spacing: 2px; text-transform: uppercase; white-space: nowrap;
  }
  .detail {
    font-family: 'Oswald', sans-serif; font-weight: 300; font-size: 24px;
    color: var(--text); letter-spacing: 1px; white-space: nowrap;
  }
  .detail-small { font-size: 20px; }
  .tagline {
    font-family: 'Open Sans', sans-serif; font-weight: 700; font-size: 21px;
    color: var(--navy-ink); white-space: nowrap;
  }
</style>
</head>
<body>
<main class="canvas">
  <section class="card card-front">
    <div class="brand-frame"><span class="brand-name">Kelvor Engineers</span></div>
    <p class="brand-cities">Atlanta | Charlotte | Houston | San Antonio</p>
  </section>

  <section class="card card-back">
    <div class="contact-table">
      <div class="row"><span class="person-name">Dana Rowe Hollis</span></div>
      <div class="row row-split">
        <div class="cell"><span class="detail">Cell: 555.201.4470</span></div>
        <div class="cell"><span class="detail">Tel: 555.201.4400</span></div>
      </div>
      <div class="row"><span class="detail detail-small">DHOLLIS@kelvorstruct.com | www.kelvorstruct.com</span></div>
      <div class="row"><span class="tagline">Multi-discipline engineering www.kelvorstruct.com</span></div>
    </div>
  </section>
</main>
</body>
</html>
```